"Fight Back" banner ad design

We have sketched the design and have images to consider including. We are looking for something striking, FIGHT BACK! with a clenched fist image, then a fading images of variance.png and hi-bill.png in the background. Tag line "Fight your water bill with your own data" optionally include "Tally Mode" rivo3196 logo, KPMT Design, LLC based in San Diego CA. Pre-order now, visit https://www.fundbeacon.com/rivometer @rivo3196, info@rivo3196.com

"Fight your water bill with your own data"

```html
<!DOCTYPE html>
<html lang="en">
<head>
<meta charset="utf-8">
<title>Fight Back – Water Bill Banner</title>
<link rel="stylesheet" href="https://fonts.googleapis.com/css2?family=Montserrat:wght@700;800&family=Lexend:wght@500;600&family=Arimo:wght@400;700&display=swap">
<style>
  :root {
    --teal: #38788a;
    --teal-dark: #245a6a;
    --teal-light: #88c9db;
    --navy: #1d466c;
    --ink: #161616;
    --white: #ffffff;
    --skin-light: #efd0b6;
    --skin-mid: #e2b493;
    --paper: #f4f6f7;
    --button-top: #4d9ed6;
    --button-bottom: #2467a8;
    --button-frame: #e4eef5;
  }
  * { box-sizing: border-box; margin: 0; padding: 0; }
  html, body { width: 1200px; height: 663px; overflow: hidden; background: var(--white); }
  .banner { position: relative; width: 1200px; height: 663px; overflow: hidden; background: var(--white); }

  .brand { position: absolute; left: 50px; top: 20px; display: flex; flex-direction: column; align-items: center; }
  .brand-mark { width: 56px; height: 56px; border-radius: 50%; background: var(--teal-light); margin-bottom: 8px; }
  .brand-name { font-family: "Lexend", sans-serif; font-weight: 600; font-size: 22px; color: var(--teal); }

  .bill-photo {
    position: absolute; left: 0; top: 106px; width: 740px; height: 170px;
    background: linear-gradient(90deg, var(--teal-light) 0 3%, var(--paper) 3% 96%, var(--teal-dark) 96% 100%);
  }
  .fist-photo {
    position: absolute; left: 168px; top: 80px; width: 410px; height: 583px;
    border-radius: 40px 40px 0 0;
    background: radial-gradient(ellipse at 50% 30%, var(--skin-light), var(--skin-mid) 75%, rgba(226,180,147,0) 100%);
  }

  .headline {
    position: absolute; left: 226px; top: 14px;
    font-family: "Montserrat", sans-serif; font-weight: 800; font-size: 128px; line-height: 1;
    letter-spacing: -5px; color: var(--teal);
    -webkit-text-stroke: 8px var(--white); paint-order: stroke fill;
  }
  .tagline {
    position: absolute; left: 752px; top: 142px; width: 440px;
    font-family: "Lexend", sans-serif; font-weight: 600; font-size: 39px; line-height: 56px;
    color: var(--navy); letter-spacing: -1.2px; white-space: nowrap;
  }

  .chart { position: absolute; left: 560px; top: 282px; width: 636px; height: 381px; }

  .pitch {
    position: absolute; left: 14px; top: 408px;
    font-family: "Lexend", sans-serif; font-weight: 500; font-size: 29px; line-height: 40px;
    color: var(--ink); letter-spacing: -1px;
    text-shadow: 0 0 6px var(--white), 0 0 6px var(--white), 2px 3px 4px rgba(0,0,0,.35);
  }
  .preorder-frame {
    position: absolute; left: 6px; top: 496px; width: 405px; height: 66px;
    background: var(--button-frame); border-radius: 4px;
  }
  .preorder {
    position: absolute; left: 18px; top: 504px; width: 382px; height: 50px;
    background: linear-gradient(var(--button-top), var(--button-bottom));
    border-radius: 3px; color: var(--white);
    font-family: "Lexend", sans-serif; font-weight: 500; font-size: 35px; line-height: 50px;
    text-align: center; letter-spacing: -0.5px; text-decoration: none;
  }
  .preorder .arrow { margin-left: 22px; }
  .contact {
    position: absolute; left: 14px;
    font-family: "Lexend", sans-serif; font-weight: 500; font-size: 28px; line-height: 36px;
    color: var(--ink); letter-spacing: -0.8px; white-space: pre;
    text-shadow: 0 0 6px var(--white), 0 0 6px var(--white), 2px 3px 4px rgba(0,0,0,.35);
  }
  .contact-visit { top: 568px; }
  .contact-social { top: 608px; display: flex; align-items: center; }
  .social-dot { width: 42px; height: 42px; border-radius: 50%; background: var(--navy); margin-right: 14px; margin-left: 4px; }
</style>
</head>
<body>
<main class="banner">
  <div class="bill-photo" role="img" aria-label="Water bill strip showing fees, charges and total due"></div>
  <div class="fist-photo" role="img" aria-label="Photo of a clenched fist crumpling a water bill"></div>

  <div class="brand">
    <span class="brand-mark"></span>
    <span class="brand-name">Rivo3196</span>
  </div>

  <h1 class="headline">FIGHT BACK!</h1>
  <p class="tagline">Fight your water bill<br>with your own data.</p>

  <svg class="chart" viewBox="700 352 795 476" role="img" aria-label="Bar chart of water use in hundred cubic feet, previous year versus current year">
    <rect x="700" y="352" width="795" height="476" fill="#fff"/>
    <rect x="700" y="352" width="795" height="476" fill="none" stroke="#245a6a" stroke-width="3"/>
    <rect x="700" y="352" width="795" height="40" fill="#245a6a"/>
    <text x="1097" y="382" text-anchor="middle" font-family="Arimo, sans-serif" font-weight="700" font-size="27" fill="#fff">WATER USE IN HCF (Hundred Cubic Feet)</text>
    <rect x="905" y="398" width="22" height="22" fill="#88c9db" stroke="#245a6a"/>
    <text x="948" y="415" font-family="Arimo, sans-serif" font-size="19" fill="#161616">Previous Year</text>
    <rect x="1112" y="398" width="22" height="22" fill="#245a6a"/>
    <text x="1153" y="415" font-family="Arimo, sans-serif" font-size="19" fill="#161616">Current Year</text>
    <g stroke="#161616" stroke-width="2">
      <line x1="745" y1="430" x2="1480" y2="430"/><line x1="745" y1="455" x2="1480" y2="455"/>
      <line x1="745" y1="479" x2="1480" y2="479"/><line x1="745" y1="504" x2="1480" y2="504"/>
      <line x1="745" y1="529" x2="1480" y2="529"/><line x1="745" y1="553" x2="1480" y2="553"/>
      <line x1="745" y1="578" x2="1480" y2="578"/><line x1="745" y1="603" x2="1480" y2="603"/>
      <line x1="745" y1="627" x2="1480" y2="627"/><line x1="745" y1="652" x2="1480" y2="652"/>
      <line x1="745" y1="677" x2="1480" y2="677"/><line x1="745" y1="701" x2="1480" y2="701"/>
      <line x1="745" y1="726" x2="1480" y2="726"/><line x1="745" y1="751" x2="1480" y2="751"/>
      <line x1="745" y1="775" x2="1480" y2="775"/><line x1="745" y1="800" x2="1480" y2="800"/>
    </g>
    <g font-family="Arimo, sans-serif" font-size="17" fill="#161616" text-anchor="end">
      <text x="738" y="437">80</text><text x="738" y="461">75</text><text x="738" y="486">70</text>
      <text x="738" y="511">65</text><text x="738" y="535">60</text><text x="738" y="560">55</text>
      <text x="738" y="585">50</text><text x="738" y="609">45</text><text x="738" y="634">40</text>
      <text x="738" y="659">35</text><text x="738" y="683">30</text><text x="738" y="708">25</text>
      <text x="738" y="733">20</text><text x="738" y="757">15</text><text x="738" y="782">10</text>
      <text x="738" y="807">5</text><text x="738" y="831">0</text>
    </g>
    <g fill="#88c9db" stroke="#245a6a" stroke-width="1.5">
      <rect x="805" y="691" width="25" height="137"/>
      <rect x="930" y="656" width="25" height="172"/>
      <rect x="1053" y="732" width="25" height="96"/>
      <rect x="1177" y="678" width="25" height="150"/>
      <rect x="1302" y="701" width="25" height="127"/>
      <rect x="1425" y="701" width="25" height="127"/>
    </g>
    <g fill="#245a6a" stroke="#163c48" stroke-width="1.5">
      <rect x="837" y="711" width="25" height="117"/>
      <rect x="960" y="726" width="25" height="102"/>
      <rect x="1085" y="726" width="25" height="102"/>
      <rect x="1208" y="434" width="25" height="394"/>
      <rect x="1333" y="489" width="25" height="339"/>
      <rect x="1456" y="464" width="25" height="364"/>
    </g>
  </svg>

  <p class="pitch">A San Diego startup<br>patent pending</p>

  <div class="preorder-frame"></div>
  <a class="preorder" href="https://www.fundbeacon.com/rivometer">Pre-order now<span class="arrow">›</span></a>

  <p class="contact contact-visit">Visit :  fundbeacon  /  rivometer.com</p>
  <p class="contact contact-social"><span class="social-dot"></span>@rivo3196 / info@rivo3196.com</p>
</main>
</body>
</html>
```